Design a calming beauty medical salon & spa website based in Hong Kong

We need help building an informational website for a beauty salon in Hong Kong. The local salon provides facials, massages, body and other slimming treatments in a relaxing environment. We offer some non-invasive medical treatments, such as botox. Having built the business on word of mouth, it is now time for us to launch a website to help market the business better. Website requirements:

-Must be responsive
-Use vibrant but clean colours. not too many, 1-2 colours
-Must be bilingual (switch between Chinese traditional and English)
-Our current website is host on a server, not using any particular platforms like wordpress

Pages:
1/ Homepage
2/ About us (incorporate gallery of salon photos and history of company)
3/ Promotions and latest deals (and leads them to sign up for more info, maybe pop-up small window when you click on a promotion)
4/ Treatment menus
4.1/Body treatments
4.2/ Face treatments
4.3/ Slimming treatments
5/ Showcasing products sold (no e-commerce functionality, just showing off products)
6/ Contact us (tel, address, map, opening hrs)

Footer - must haves include contact us info, privacy policy, terms & conditions, copyright blurb, join our company/employment page (with a form)

For information (comparable websites we like):
http://veltora.com/
http://pambrix.com.hk/tc/aboutpambrix/background.php#centerenvi
Attaching a very first draft concept for this website
Attaching pictures of the beauty salon
Attaching logo

Target Market(s)

Hong Kong based, Chinese, females, 30-50+ age. 90% female clients.

Industry/Entity Type

Beauty Salon

Number of Pages Required

5+ page

Font styles to use
Sans Serif

Colors
f9d9e8
fbd3d4
fee3d5
fbe7d2
fee18a
fbf289
ffffff

Requirements
Must have
• interactive elements on website, such as scrolling banner photo headers
• incorporate photos of website salon
• connect to facebook page

```html
<!DOCTYPE html>
<html lang="en">
<head>
<meta charset="utf-8">
<title>Lumen Beauty – Submit Your Information</title>
<link rel="stylesheet" href="https://fonts.googleapis.com/css2?family=Signika:wght@300;400;600;700&display=swap">
<style>
:root{
  --ink:#1c1c1c;
  --plum:#5b1a63;
  --rose:#c4968f;
  --rose-line:#d8a7a0;
  --field:#fbe6e2;
  --field-line:#f0cfca;
  --modal:#fdf7fb;
  --nav:#f2ccc6;
  --nav-active:#d9aba4;
  --footer:#c89ea0;
  --footer-ink:#2a1d1e;
  --bar:#000;
  --scrim:rgba(0,0,0,.45);
}
*{box-sizing:border-box;margin:0;padding:0}
html,body{width:1193px;height:1200px;overflow:hidden}
body{position:relative;background:#fff;font-family:"Signika",sans-serif;color:var(--ink)}

/* header */
.top-tab{position:absolute;left:437px;top:0;width:756px;height:35px;background:#f3e3e1;border-bottom-left-radius:22px;box-shadow:0 2px 4px rgba(0,0,0,.25);font-size:13px;letter-spacing:1.5px}
.top-tab span{position:absolute;top:10px;display:flex;align-items:center;gap:7px}
.tab-email{left:65px}.tab-page{left:290px}.tab-lang{left:597px;letter-spacing:2px}
.tab-sep{position:absolute;top:10px;width:1px;height:16px;background:#bbb}
.logo{position:absolute;left:86px;top:30px;display:flex;align-items:center;gap:10px;font-size:31px;font-weight:600;color:var(--plum)}
.logo i{display:block;width:44px;height:44px;border-radius:50%;background:var(--plum)}
.contact-block{position:absolute;top:60px;font-size:16px;letter-spacing:1.5px;line-height:21px}
.contact-tel{left:518px}.contact-hours{left:788px}
.head-icon{position:absolute;top:63px}

.nav{position:absolute;left:0;top:125px;width:1193px;height:35px;background:var(--nav)}
.nav a{position:absolute;top:0;height:35px;line-height:35px;font-size:16px;letter-spacing:1.8px;color:var(--ink);text-decoration:none}
.nav .active{background:var(--nav-active);padding:0 26px;left:384px}

/* footer */
.footer{position:absolute;left:0;top:819px;width:1193px;height:353px;background:var(--footer);color:var(--footer-ink);font-size:14px;letter-spacing:.5px}
.foot-item{position:absolute;left:86px;display:flex;align-items:center;gap:10px}
.foot-item i{display:flex;align-items:center;justify-content:center;width:25px;height:25px;border-radius:50%;background:#111}
.foot-about{position:absolute;left:463px;top:188px;width:280px;line-height:21px}
.foot-links{position:absolute;left:871px;top:186px;list-style:none;line-height:23px}
.copyright{position:absolute;left:0;top:1172px;width:1193px;height:28px;background:var(--bar);color:#ccc;font-size:14px;text-align:center;line-height:28px;letter-spacing:.5px}

.scrim{position:absolute;inset:0;background:var(--scrim)}

/* modal */
.modal{position:absolute;left:86px;top:198px;width:1022px;height:803px;background:var(--modal)}
.close{position:absolute;right:9px;top:9px;width:28px;height:28px;border-radius:50%;background:#c9c7c9;display:flex;align-items:center;justify-content:center}
.modal-title{position:absolute;top:54px;width:100%;text-align:center;font-size:32px;font-weight:700;letter-spacing:3px}
.divider{position:absolute;left:460px;top:304px}
.field{position:absolute;height:36px;background:var(--field);border:1px solid var(--field-line);font-size:13px;letter-spacing:1px;padding-left:16px;line-height:34px}
.field.select::after{content:"";position:absolute;right:16px;top:14px;border-left:7px solid transparent;border-right:7px solid transparent;border-top:7px solid var(--rose)}
.full{left:42px;width:935px}.half-l{left:42px;width:456px}.half-r{left:523px;width:454px}
.terms{position:absolute;left:42px;top:517px;font-size:12.5px;line-height:21px;letter-spacing:.6px}
.agree{position:absolute;left:45px;top:652px;display:flex;align-items:center;gap:9px;font-size:13px;letter-spacing:.6px}
.agree i{width:21px;height:21px;background:var(--rose)}
.submit{position:absolute;left:429px;top:699px;width:162px;height:44px;background:var(--rose);color:#fff;font-size:16px;font-weight:600;letter-spacing:2px;display:flex;align-items:center;justify-content:center;border-radius:14px 0 14px 0}
</style>
</head>
<body>
<header>
  <div class="top-tab">
    <span class="tab-email"><svg width="15" height="11" viewBox="0 0 15 11"><rect width="15" height="11" fill="#222"/><path d="M0 0l7.5 6L15 0" stroke="#f3e3e1" fill="none" stroke-width="1.4"/></svg>Email Us</span>
    <i class="tab-sep" style="left:218px"></i>
    <span class="tab-page"><svg width="12" height="12"><rect width="12" height="12" rx="2" fill="#222"/></svg>Connect on our Page</span>
    <i class="tab-sep" style="left:528px"></i>
    <span class="tab-lang">ENG | CN</span>
  </div>
  <div class="logo"><i></i>Lumen Beauty</div>
  <svg class="head-icon" style="left:467px" width="34" height="34" viewBox="0 0 34 34"><path d="M8 4l6 6-4 4c2 5 5 8 10 10l4-4 6 6-5 5C14 30 4 20 3 9z" fill="none" stroke="#555" stroke-width="2.4" stroke-linejoin="round"/></svg>
  <div class="contact-block contact-tel">TEL: 2345 6781<br>WHATSAPP: 6123 4580</div>
  <svg class="head-icon" style="left:740px" width="34" height="34" viewBox="0 0 34 34"><rect x="2" y="5" width="24" height="22" rx="2" fill="none" stroke="#555" stroke-width="2"/><path d="M2 11h24M8 2v6M20 2v6" stroke="#555" stroke-width="2"/><circle cx="25" cy="25" r="7" fill="#fff" stroke="#555" stroke-width="2"/><path d="M25 21v4h3" stroke="#555" stroke-width="1.6" fill="none"/></svg>
  <div class="contact-block contact-hours">MON TO FRI: 10.30 AM TO 9.30PM<br>SAT AND HOLIDAY: 10.30 AM TO 7.30PM</div>
  <nav class="nav">
    <a style="left:112px">HOME</a>
    <a style="left:241px">ABOUT US</a>
    <a class="active">PROMOTIONS</a>
    <a style="left:608px">TREATMENT</a>
    <a style="left:799px">PRODUCTS</a>
    <a style="left:973px">CONTACT US</a>
  </nav>
</header>

<footer class="footer">
  <div class="foot-item" style="top:170px"><i></i>2345 6781</div>
  <div class="foot-item" style="top:205px"><i><svg width="12" height="12" viewBox="0 0 34 34"><path d="M8 4l6 6-4 4c2 5 5 8 10 10l4-4 6 6-5 5C14 30 4 20 3 9z" fill="#fff"/></svg></i>6123 4588</div>
  <div class="foot-item" style="top:240px"><i><svg width="12" height="9" viewBox="0 0 15 11"><rect width="15" height="11" fill="#fff"/><path d="M0 0l7.5 6L15 0" stroke="#111" fill="none" stroke-width="1.4"/></svg></i>hello@lumenbeauty.com.hk</div>
  <div class="foot-item" style="top:275px"><i></i>Connect on our Page</div>
  <p class="foot-about">exceptional knowledge and service, for tailor made treatments, customized to meet your specific needs.</p>
  <ul class="foot-links"><li>Facial Treatments</li><li>Slimming Treatments</li><li>Products</li><li>Contact Us</li><li>Join Us</li></ul>
</footer>
<div class="copyright">Copyright © 2018 Lumen Beauty HK Ltd. All Rights Reserved. Privacy Policy | Terms of Use</div>

<div class="scrim"></div>

<section class="modal">
  <div class="close"><svg width="14" height="14"><path d="M1 1l12 12M13 1L1 13" stroke="#fff" stroke-width="1.6"/></svg></div>
  <h1 class="modal-title">SUBMIT YOUR INFORMATION</h1>
  <svg class="divider" style="left:460px;top:103px;position:absolute" width="102" height="20"><path d="M0 10h30M72 10h30" stroke="var(--rose-line)" stroke-width="1.2"/><circle cx="51" cy="10" r="8" fill="none" stroke="var(--rose-line)" stroke-width="1.6"/></svg>
  <div class="field full" style="top:151px">Lorem</div>
  <div class="field half-l select" style="top:212px">Lorem</div>
  <div class="field half-r select" style="top:212px">Lorem</div>
  <div class="field half-l" style="top:273px">Lorem</div>
  <div class="field half-r" style="top:273px">Lorem</div>
  <div class="field full select" style="top:335px">Lorem ipsum simple dummy text</div>
  <div class="field full select" style="top:396px">Lorem ipsum simple</div>
  <div class="field full select" style="top:457px">Lorem ipsum</div>
  <p class="terms">
    I have read and agree to the above precautions, preferential terms and conditions and privacy policy.<br>
    I am not willing to continue to receive Lumen Beauty's product information and promotional materials in the future.<br>
    I am not willing to continue to receive all AURELLE Group's brand promotion information in the future.<br>
    (If you choose to refuse to accept, I will not receive any gifts, discounts and other discounts from your company.)<br>
    ** Offer is valid for Female customers who are at least 18 years old and first try Lumen Beauty<br>
    ** Free Experience: There are no extra and hidden costs; to purchase a course other than the free trial, you have to pay for it yourself.
  </p>
  <label class="agree"><i></i>I agree</label>
  <div class="submit">SUBMIT</div>
</section>
</body>
</html>
```